Pellowar

We need logo and wesbsite for a software development company based out of Hyderabad, India focused on startups and mid sized companies focused on build a new software products in USA and Europe countires.

Target Market(s)

startup and midsized companies in teh USA and Europe for software product development.

Industry/Entity Type

software development

Coding

Coded - Design and coding required

Number of Pages Required

5+ page

Requirements
Must have
• latest design concepts and very elegant
Nice to have
• each page should have images that reflects the content
Should not have
• too many colors

```html
<!DOCTYPE html>
<html lang="en">
<head>
<meta charset="utf-8">
<title>Pellowar — Software Product Development</title>
<link href="https://fonts.googleapis.com/css2?family=Montserrat:wght@400;500;600;700&family=Overpass:wght@600;700;800&display=swap" rel="stylesheet">
<style>
:root{
  --blue:#1a5eb0;
  --blue-dark:#0d4a95;
  --blue-mid:#2f78c8;
  --blue-light:#6c9ed6;
  --black:#000;
  --ink:#1e1e1e;
  --text:#4a4a4a;
  --grey-panel:#ececec;
  --grey-bg:#f3f3f3;
  --white:#fff;
}
*{box-sizing:border-box;margin:0;padding:0}
html,body{width:1200px;height:4071px;overflow:hidden}
body{font-family:"Montserrat",sans-serif;color:var(--text);background:var(--white);position:relative}
.abs{position:absolute}
h1,h2,h3{font-family:"Overpass",sans-serif;color:var(--ink);font-weight:700}
.btn{position:absolute;display:flex;align-items:center;justify-content:space-between;background:var(--blue);color:var(--white);font-size:12px;font-weight:600;letter-spacing:.3px;padding:0 10px 0 18px;height:36px;width:150px;border:2px solid #8db4e2}
.btn .arr{width:24px;height:24px;border-radius:50%;background:var(--white);display:flex;align-items:center;justify-content:center}

/* header */
.topbar{position:absolute;left:0;top:0;width:1200px;height:65px;background:var(--black)}
.brand{position:absolute;left:112px;top:14px;font-family:"Montserrat",sans-serif;font-weight:700;font-size:30px;color:var(--white);letter-spacing:.5px}
.contact-item{position:absolute;top:24px;color:var(--white);font-size:13px;display:flex;align-items:center;gap:10px}
.divider-v{position:absolute;top:20px;width:1px;height:24px;background:#555}
.social{position:absolute;top:17px;width:33px;height:33px;border-radius:50%;border:1.5px solid #bbb}
.nav{position:absolute;top:78px;left:0;width:1200px;height:30px;z-index:3}
.nav a{position:absolute;color:var(--white);font-size:13.5px;font-weight:600;text-decoration:none}
.nav a.active{color:#7fb0ea;border-bottom:2px solid #7fb0ea;padding-bottom:6px}

/* hero */
.hero{position:absolute;left:0;top:65px;width:1200px;height:578px;background:linear-gradient(90deg,#1d2a36 0%,#3b4a56 40%,#6f7a82 70%,#8b8f93 100%)}
.hero-title{position:absolute;left:110px;top:175px;font-family:"Montserrat",sans-serif;font-size:46px;font-weight:600;color:var(--white);letter-spacing:.5px}
.hero-sub{position:absolute;left:112px;top:236px;width:420px;font-size:16.5px;line-height:24px;color:var(--white)}
.hero .btn{left:112px;top:310px;width:215px;height:47px;font-size:15px;border:none;padding:0 14px 0 22px}
.dots{position:absolute;left:111px;top:383px;display:flex;gap:8px;align-items:center}
.dots i{width:11px;height:11px;border-radius:50%;border:1.5px solid #ddd;display:block}
.dots i.on{width:17px;height:17px;border-color:var(--white);background:radial-gradient(var(--blue-mid) 45%,transparent 50%)}
.hero-arrow{position:absolute;top:227px;width:58px;height:58px;border-radius:50%;border:1.5px solid rgba(255,255,255,.7);display:flex;align-items:center;justify-content:center}

/* about */
.about{position:absolute;left:0;top:643px;width:1200px;height:580px;background:var(--white)}
.about-panel{position:absolute;left:372px;top:75px;width:716px;height:505px;background:var(--grey-panel)}
.about-photo-frame{position:absolute;left:174px;top:150px;width:419px;height:344px;background:var(--blue)}
.about-photo{position:absolute;left:166px;top:143px;width:419px;height:344px;background:linear-gradient(135deg,#3e4a55,#8a9199 55%,#c4b48a)}
.about h2{position:absolute;left:616px;top:132px;font-size:42px}
.about p{position:absolute;left:616px;top:190px;width:452px;font-size:14.5px;line-height:25.6px}

/* product */
.product{position:absolute;left:0;top:1223px;width:1200px;height:830px;background:linear-gradient(180deg,#dcdcdc 0%,#f2f2f2 45%,#f7f7f7 100%)}
.product h2{position:absolute;left:0;width:1200px;top:75px;text-align:center;font-size:44px}
.product p{position:absolute;left:200px;width:800px;text-align:center;font-size:14.5px;line-height:25.6px;color:#333}
.wheel{position:absolute;left:428px;top:257px;width:344px;height:344px;border-radius:50%;
  background:conic-gradient(from 154.3deg,#2a67b8 0 50.4deg,#fff 0 51.4deg,#2f7fd0 0 101.8deg,#fff 0 102.8deg,#3f8ad6 0 153.2deg,#fff 0 154.2deg,#2c6fc0 0 204.6deg,#fff 0 205.6deg,#1f5fb0 0 256deg,#fff 0 257deg,#15509c 0 307.4deg,#fff 0 308.4deg,#1a59a8 0 359deg,#fff 0 360deg)}
.wheel-core{position:absolute;left:510px;top:339px;width:180px;height:180px;border-radius:50%;background:var(--white);display:flex;align-items:center;justify-content:center;font-weight:700;font-size:20px;color:var(--blue)}
.role{position:absolute;font-size:14.5px;font-weight:600;color:var(--ink)}
.role.r{text-align:right;width:300px}

/* team */
.team{position:absolute;left:0;top:2053px;width:1200px;height:490px;background:linear-gradient(180deg,#7aa8dc,#5d8fcb)}
.team-photo{position:absolute;left:0;top:0;width:1200px;height:490px}
.team h2{position:absolute;left:108px;top:70px;font-size:44px}
.team p{position:absolute;left:115px;width:455px;font-size:14.5px;line-height:25.6px;color:#16305a}

/* case study */
.case{position:absolute;left:0;top:2543px;width:1200px;height:664px;background:var(--white)}
.case-photo{position:absolute;left:111px;top:85px;width:577px;height:489px;background:linear-gradient(135deg,#2b2622,#5a4a3c 50%,#a89480)}
.case-card{position:absolute;left:594px;top:125px;width:481px;height:409px;background:var(--white);box-shadow:0 4px 20px rgba(0,0,0,.12)}
.case h2{position:absolute;left:620px;top:162px;font-size:32px}
.case p{position:absolute;left:620px;top:210px;width:440px;font-size:14px;line-height:24.5px}

/* contact */
.contact{position:absolute;left:0;top:3207px;width:1200px;height:491px;background:var(--grey-bg)}
.contact .mark{position:absolute;left:112px;top:100px;font-size:28px;font-weight:700;color:var(--blue)}
.contact h2{position:absolute;left:112px;top:196px;width:330px;font-size:33px;line-height:45px;color:#111}
.contact .lead{position:absolute;left:112px;top:306px;font-size:19px;line-height:34px;color:#222}
.lbl{position:absolute;font-size:12px;font-weight:500;color:#333;letter-spacing:.3px}
.field{position:absolute;height:35px;background:#dedede;border:1px solid #d0d0d0;font-size:11px;color:#777;padding:11px 9px}

/* footer */
.footer{position:absolute;left:0;top:3698px;width:1200px;height:373px;background:var(--black);color:var(--white)}
.footer .fbrand{position:absolute;left:112px;top:170px;font-size:34px;font-weight:600;color:var(--blue-mid);letter-spacing:.5px}
.fcol{position:absolute;top:70px}
.fcol h3{font-family:"Montserrat",sans-serif;font-size:19px;font-weight:700;color:var(--white);padding-bottom:12px;position:relative}
.fcol h3::after{content:"";position:absolute;left:0;bottom:0;width:48px;height:2px;background:var(--blue-mid)}
.fcol ul{list-style:none;margin-top:14px}
.fcol li{font-size:13px;line-height:26px}
.cinfo{display:flex;gap:10px;margin-top:14px;font-size:13px;line-height:18px}
.cinfo small{display:block;font-size:10px;color:#aaa;line-height:13px}
.frule{position:absolute;left:112px;top:302px;width:976px;height:1px;background:#444}
.fbottom{position:absolute;top:316px;font-size:12.5px}
.totop{position:absolute;left:1121px;top:247px;width:44px;height:44px;border-radius:50%;background:var(--blue-mid);display:flex;align-items:center;justify-content:center}
</style>
</head>
<body>

<!-- Header -->
<header class="topbar">
  <div class="brand">PELLOWAR</div>
  <div class="contact-item" style="left:503px">
    <svg width="14" height="14" viewBox="0 0 24 24" fill="#fff"><path d="M6.6 10.8a15 15 0 006.6 6.6l2.2-2.2a1 1 0 011-.25 11.4 11.4 0 003.6.57 1 1 0 011 1V20a1 1 0 01-1 1A17 17 0 013 4a1 1 0 011-1h3.5a1 1 0 011 1 11.4 11.4 0 00.57 3.6 1 1 0 01-.25 1z"/></svg>
    <span>+1 (555) 014 2290</span>
  </div>
  <div class="divider-v" style="left:682px"></div>
  <div class="contact-item" style="left:715px">
    <svg width="15" height="11" viewBox="0 0 24 18" fill="#fff"><path d="M0 0h24v18H0z" fill="none" stroke="#fff" stroke-width="2"/><path d="M0 0l12 10L24 0" fill="none" stroke="#fff" stroke-width="2"/></svg>
    <span>hello@pellowar-mail.com</span>
  </div>
  <div class="divider-v" style="left:940px"></div>
  <span class="social" style="left:961px"></span>
  <span class="social" style="left:1003px"></span>
  <span class="social" style="left:1045px"></span>
</header>

<!-- Hero -->
<section class="hero" role="img" aria-label="Photo of two smiling business colleagues reviewing a tablet in a modern office">
  <h1 class="hero-title">PELLOWAR</h1>
  <p class="hero-sub">Teams are the essence of every business. They can create wonders if built with perfection.</p>
  <a class="btn">GET STARTED <span class="arr"><svg width="14" height="14" viewBox="0 0 24 24"><path d="M4 12h14M12 6l6 6-6 6" stroke="#1a5eb0" stroke-width="3" fill="none"/></svg></span></a>
  <div class="dots"><i></i><i class="on"></i><i></i><i></i></div>
  <div class="hero-arrow" style="left:24px"><svg width="20" height="20" viewBox="0 0 24 24"><path d="M20 12H5M11 6l-6 6 6 6" stroke="#fff" stroke-width="2" fill="none"/></svg></div>
  <div class="hero-arrow" style="left:1117px"><svg width="20" height="20" viewBox="0 0 24 24"><path d="M4 12h15M13 6l6 6-6 6" stroke="#fff" stroke-width="2" fill="none"/></svg></div>
</section>
<nav class="nav">
  <a class="active" style="left:262px">Home</a>
  <a style="left:344px">About Us</a>
  <a style="left:448px">Our Services</a>
  <a style="left:575px">Case Study</a>
  <a style="left:693px">Build Your Team</a>
  <a style="left:845px">Build Your Product</a>
  <a style="left:1012px">Contact Us</a>
</nav>

<!-- About -->
<section class="about">
  <svg class="abs" style="left:0;top:0" width="460" height="580"><polygon points="0,0 365,0 456,580 0,580" fill="#0f5db4"/></svg>
  <div class="about-panel"></div>
  <div class="about-photo-frame"></div>
  <div class="about-photo" role="img" aria-label="Photo of three smiling professionals standing together in an office"></div>
  <h2>About Us</h2>
  <p>We are a group of entrepreneurs, technocrats, software architects, and delivery heads who have come together to serve startups, product companies, and enterprises with their product development. We are prompt in understanding your product and help design, build, maintain and operate your product. Pellowar quickly set up a team of UX experts, Business Analysts, Developers and QA resources to build the best team to deliver the product.</p>
  <a class="btn" style="left:616px;top:420px">LEARN MORE <span class="arr"><svg width="12" height="12" viewBox="0 0 24 24"><path d="M4 12h14M12 6l6 6-6 6" stroke="#1a5eb0" stroke-width="3" fill="none"/></svg></span></a>
</section>

<!-- Build Your Product -->
<section class="product">
  <h2>Build Your Product</h2>
  <p style="top:136px">As startups are racing to build software as a product, they have stumbling blocks on building software from scratch. One of the reasons is stiff competition.</p>
  <p style="top:202px">The competition to get the best resources, robust design, and scalable technology is overwhelming.</p>
  <svg class="abs" style="left:0;top:0" width="1200" height="830">
    <g stroke="#2a67b8" stroke-width="1.3" fill="none">
      <path d="M350 304H458V337"/><path d="M850 304H742V337"/>
      <path d="M350 432H430"/><path d="M850 432H770"/>
      <path d="M350 559H458V525"/><path d="M850 559H742V525"/>
      <path d="M600 601V636"/>
    </g>
    <g fill="#2a67b8">
      <circle cx="350" cy="304" r="3.5"/><circle cx="850" cy="304" r="3.5"/>
      <circle cx="350" cy="432" r="3.5"/><circle cx="850" cy="432" r="3.5"/>
      <circle cx="350" cy="559" r="3.5"/><circle cx="850" cy="559" r="3.5"/>
      <circle cx="600" cy="638" r="3.5"/>
    </g>
  </svg>
  <div class="wheel"></div>
  <div class="wheel-core">PELLOWAR</div>
  <span class="role r" style="left:30px;top:295px">Testers</span>
  <span class="role" style="left:865px;top:295px">Project Manager</span>
  <span class="role r" style="left:30px;top:423px">Technical/Content Writers</span>
  <span class="role" style="left:865px;top:423px">Team Lead</span>
  <span class="role r" style="left:30px;top:550px">UX Experts</span>
  <span class="role" style="left:865px;top:550px">Business analyst</span>
  <span class="role" style="left:0;width:1200px;text-align:center;top:650px">Developers</span>
  <a class="btn" style="left:525px;top:707px">LEARN MORE <span class="arr"><svg width="12" height="12" viewBox="0 0 24 24"><path d="M4 12h14M12 6l6 6-6 6" stroke="#1a5eb0" stroke-width="3" fill="none"/></svg></span></a>
</section>

<!-- Build Your Team -->
<section class="team">
  <svg class="team-photo" width="1200" height="490" role="img" aria-label="Photo of a diverse team shaking hands and applauding around a laptop">
    <defs><linearGradient id="teamPhoto" x1="0" y1="0" x2="1" y2="1"><stop offset="0" stop-color="#3c4756"/><stop offset=".5" stop-color="#8a8f98"/><stop offset="1" stop-color="#d7d8db"/></linearGradient></defs>
    <polygon points="787,0 1200,0 1200,490 325,490" fill="url(#teamPhoto)"/>
  </svg>
  <h2>Build Your Team</h2>
  <p style="top:128px">Break free from traditional recruiting with us. At Pellowar, we help you achieve the right organizational matrix with rockstars who can take your business to the next level.</p>
  <p style="top:210px;width:395px">We have spent years trying to innovate and improve the process of hiring talented individuals who can take businesses to the next level. We ensure that the workforce we employ for your organization is highly productive and takes you to the golden standards of heights.</p>
  <a class="btn" style="left:115px;top:379px">LEARN MORE <span class="arr"><svg width="12" height="12" viewBox="0 0 24 24"><path d="M4 12h14M12 6l6 6-6 6" stroke="#1a5eb0" stroke-width="3" fill="none"/></svg></span></a>
</section>

<!-- Case Study -->
<section class="case">
  <div class="case-photo" role="img" aria-label="Photo of two colleagues working together on a laptop"></div>
  <div class="case-card"></div>
  <h2>Case study</h2>
  <p>Many business owners have great ideas but no experience with the actual product. Once you have an idea in mind, you will require software development aid at some point – whether your concept is for next-generation software or an inventive approach to offering an existing service. It might also be the development of a mobile app or web-based software. Whatever product you're working on, you'll need a technical co-founder to help you get it off the ground. An MVP can help you turn your vision into reality.</p>
  <a class="btn" style="left:620px;top:452px">LEARN MORE <span class="arr"><svg width="12" height="12" viewBox="0 0 24 24"><path d="M4 12h14M12 6l6 6-6 6" stroke="#1a5eb0" stroke-width="3" fill="none"/></svg></span></a>
</section>

<!-- Contact -->
<section class="contact">
  <div class="mark">PELLOWAR</div>
  <h2>Get In Touch With Us Pellowar</h2>
  <p class="lead">Reach out to discuss your needs.<br>hello@pellowar-mail.com</p>
  <span class="lbl" style="left:498px;top:86px">YOUR NAME</span>
  <div class="field" style="left:498px;top:101px;width:254px">Jane Morrow</div>
  <span class="lbl" style="left:783px;top:86px">COMPANY</span>
  <div class="field" style="left:783px;top:101px;width:255px">jane.morrow@example.com</div>
  <span class="lbl" style="left:498px;top:166px">EMAIL ADDRESS</span>
  <div class="field" style="left:498px;top:181px;width:254px">jane.morrow@example.com</div>
  <span class="lbl" style="left:783px;top:166px">PHONE</span>
  <div class="field" style="left:783px;top:181px;width:255px">555 014 2290</div>
  <span class="lbl" style="left:498px;top:246px">MESSAGE</span>
  <div class="field" style="left:498px;top:261px;width:540px;height:100px">Hi, do you have a moment to talk abo....</div>
  <a class="btn" style="left:498px;top:367px">SUBMIT <span class="arr"><svg width="12" height="12" viewBox="0 0 24 24"><path d="M4 12h14M12 6l6 6-6 6" stroke="#1a5eb0" stroke-width="3" fill="none"/></svg></span></a>
</section>

<!-- Footer -->
<footer class="footer">
  <div class="fbrand">PELLOWAR</div>
  <div class="fcol" style="left:387px"><h3>Quick Links</h3>
    <ul><li>Home</li><li>About Us</li><li>Our Services</li><li>Case Study</li><li>Build Your Team</li><li>Build Your Product</li></ul></div>
  <div class="fcol" style="left:580px"><h3>Support</h3>
    <ul><li>Team</li><li>About Us</li><li>Careers</li><li>Our Values</li></ul></div>
  <div class="fcol" style="left:738px"><h3>Links</h3>
    <ul><li>Copyright</li><li>Legal</li><li>Privacy</li><li>Accessibility</li><li>Sitemap</li></ul></div>
  <div class="fcol" style="left:903px"><h3>Contact Us</h3>
    <div class="cinfo"><svg width="14" height="18" viewBox="0 0 24 32"><path d="M12 0a12 12 0 00-12 12c0 9 12 20 12 20s12-11 12-20A12 12 0 0012 0zm0 17a5 5 0 110-10 5 5 0 010 10z" fill="#2f78c8"/></svg><div><small>Address</small>48 Marlow Street,<br>Austin Texas, USA</div></div>
    <div class="cinfo"><svg width="14" height="14" viewBox="0 0 24 24" fill="#2f78c8"><path d="M6.6 10.8a15 15 0 006.6 6.6l2.2-2.2a1 1 0 011-.25 11.4 11.4 0 003.6.57 1 1 0 011 1V20a1 1 0 01-1 1A17 17 0 013 4a1 1 0 011-1h3.5a1 1 0 011 1 11.4 11.4 0 00.57 3.6 1 1 0 01-.25 1z"/></svg><div><small>Phone</small>+1 (555) 014 2290</div></div>
    <div class="cinfo"><svg width="14" height="11" viewBox="0 0 24 18"><path d="M0 0h24v18H0z" fill="#2f78c8"/><path d="M0 0l12 10L24 0" fill="none" stroke="#000" stroke-width="2"/></svg><div><small>Mail</small>hello@pellowar-mail.com</div></div>
  </div>
  <div class="totop"><svg width="16" height="16" viewBox="0 0 24 24"><path d="M6 15l6-6 6 6" stroke="#fff" stroke-width="2.5" fill="none"/></svg></div>
  <div class="frule"></div>
  <div class="fbottom" style="left:112px">Copyright © 2022 | All Rights Reserved</div>
  <div class="fbottom" style="left:808px;font-size:11.5px">TERMS &amp; CONDITIONS</div>
  <div class="fbottom" style="left:961px;color:var(--blue-mid)">|</div>
  <div class="fbottom" style="left:987px;font-size:11.5px">PRIVACY POLICY</div>
</footer>

</body>
</html>
```